Corvana Tongue Works, LLC

We need a business card that includes information about our business and conveys a reliable business that provides document translation services and interpreters for a variety of corporate and individual clients. We want to come across as professional, reliable, yet approachable. It should include the following on one side:

ESL / ENL Language Classes, Private Lessons, and Online Tutors
PLEXA Training and Testing
Translating & Interpreting Services
Contact us about Over-the-Phone Interpreting in over 200 languages
24/7/365
www.corvanatongue.example

The other side should include (555) 481-3062

Rhoda Pelling, President
482 Garnet Ave., Ste. 219
Indianapolis, IN 40917

Please add USA as part of the address. Also, please add rmpelling@corvanatongueworks.example as the e-mail address. Thank you.

Target Market(s)

Business professionals, their families, the international community

Industry/Entity Type

Business

Contact Information for Business Card

24/7/365
www.corvanatongue.example

(555) 481-3062

Rhoda Pelling, President
482 Garnet Ave., Ste. 219
Indianapolis, IN 40917
USA

Font styles to use
Sans Serif

Colors

Designer to choose colors to be used in the design.

Requirements
Must have
• See project description
• e-mail address and web address
• Phone number
Nice to have
• a globe
• physical address
Should not have
• Should not have the same color scheme as other agencies in our market in Indiana unless it is blue and black. No purple or yellow.

```html
<!DOCTYPE html>
<html lang="en">
<head>
<meta charset="utf-8">
<title>Corvana Tongue Works – Business Card</title>
<link href="https://fonts.googleapis.com/css2?family=Open+Sans:wght@400;600&family=Roboto:wght@400;500;700&display=swap" rel="stylesheet">
<style>
  :root{
    --bg:#2b2b2d;
    --card:#0b0b0c;
    --card-edge:#1a1a1c;
    --blue:#2a93d5;
    --white:#ffffff;
    --grey:#cfd3d8;
  }
  *{margin:0;padding:0;box-sizing:border-box}
  html,body{width:1200px;height:896px;overflow:hidden;background:var(--bg)}
  .canvas{position:relative;width:1200px;height:896px}
  .card{
    position:absolute;left:250px;width:700px;height:400px;
    background:linear-gradient(160deg,var(--card-edge) 0%,var(--card) 45%,var(--card) 100%);
    border-radius:26px;overflow:hidden;
    font-family:"Roboto",Arial,sans-serif;color:var(--white);
  }
  .card--services{top:32px}
  .card--contact{top:464px}

  /* brand lockup */
  .brand{display:flex;align-items:center;gap:16px}
  .brand__dot{width:74px;height:74px;border-radius:50%;background:var(--blue);flex:none}
  .brand__name{font-family:"Open Sans",Arial,sans-serif;font-weight:600;font-size:30px;line-height:1.05;color:var(--white);width:250px}

  /* services side */
  .card--services .brand{position:absolute;left:50%;top:46px;transform:translateX(-50%)}
  .services{position:absolute;left:0;right:0;top:170px;text-align:center;font-size:17px;line-height:1.45;font-weight:500}
  .services__rule{position:absolute;left:90px;right:90px;top:282px;height:2px;background:var(--blue)}
  .services__cta{position:absolute;left:0;right:0;top:298px;text-align:center;font-size:18px;line-height:1.45;font-weight:500}

  /* contact side */
  .card--contact .brand{position:absolute;left:48px;top:74px}
  .card--contact .brand__name{font-size:26px;width:220px}
  .person{position:absolute;right:80px;top:54px;text-align:right}
  .person__name{font-size:32px;font-weight:500;letter-spacing:.5px;color:var(--blue)}
  .person__title{font-size:16px;color:var(--grey);margin-top:4px}
  .accent{position:absolute;right:0;top:50px;height:52px;display:flex}
  .accent__white{width:8px;background:var(--white)}
  .accent__gap{width:6px}
  .accent__blue{width:40px;background:var(--blue)}
  .divider{position:absolute;left:48px;right:80px;top:196px;height:2px;background:var(--blue)}
  .address{position:absolute;right:80px;top:226px;text-align:right;font-size:18px;line-height:1.5;color:var(--grey);font-style:normal}
  .contact{position:absolute;left:48px;top:262px;list-style:none;font-size:17px;line-height:1.6;color:var(--grey)}
  .contact li{display:flex;align-items:center;gap:10px}
  .contact svg{width:15px;height:15px;flex:none}
</style>
</head>
<body>
<main class="canvas">

  <section class="card card--services">
    <div class="brand">
      <span class="brand__dot"></span>
      <span class="brand__name">Corvana Tongue Works, LLC</span>
    </div>
    <p class="services">
      ESL / ENL Language Classes, Private Lessons, and Online Tutors<br>
      PLEXA Training and Testing<br>
      Translating &amp; Interpreting Services
    </p>
    <div class="services__rule"></div>
    <p class="services__cta">
      Contact us about Over-the-Phone Interpreting in over 200 languages<br>
      24/7/365
    </p>
  </section>

  <section class="card card--contact">
    <div class="brand">
      <span class="brand__dot"></span>
      <span class="brand__name">Corvana Tongue Works, LLC</span>
    </div>

    <div class="person">
      <div class="person__name">RHODA PELLING</div>
      <div class="person__title">President</div>
    </div>
    <div class="accent"><span class="accent__white"></span><span class="accent__gap"></span><span class="accent__blue"></span></div>

    <div class="divider"></div>

    <ul class="contact">
      <li>
        <svg viewBox="0 0 16 16" aria-hidden="true"><path d="M4 1.5l2.5 3-1.6 1.6a9 9 0 005 5l1.6-1.6 3 2.5-1.8 2.5C7 14 2 9 1.5 3.3z" fill="var(--blue)"/></svg>
        (555) 481-3062
      </li>
      <li>
        <svg viewBox="0 0 16 16" aria-hidden="true"><rect x="1.5" y="3.5" width="13" height="9" rx="1" fill="none" stroke="var(--blue)" stroke-width="1.6"/><path d="M2 4l6 5 6-5" fill="none" stroke="var(--blue)" stroke-width="1.6"/></svg>
        rmpelling@corvanatongueworks.example
      </li>
      <li>
        <svg viewBox="0 0 16 16" aria-hidden="true"><circle cx="8" cy="8" r="6.5" fill="none" stroke="var(--blue)" stroke-width="1.5"/><ellipse cx="8" cy="8" rx="2.8" ry="6.5" fill="none" stroke="var(--blue)" stroke-width="1.2"/><path d="M1.5 8h13" stroke="var(--blue)" stroke-width="1.2"/></svg>
        www.corvanatongue.example
      </li>
    </ul>

    <address class="address">
      482 Garnet Ave., Ste. 219<br>
      Indianapolis, IN 40917 USA
    </address>
  </section>

</main>
</body>
</html>
```